Business Card Design for my Real Estate Investing Company

This is for a Real Estate Investing Company that will be serving the Las Vegas Valley. Id like the following slogan included: "Investing in Our Community" I have attached my logo. You will see the color tones I'm interested in..in my logo. I would like the card to be double-sided with a modern, professional look.
Target Market(s)
Homeowners, banks, real estate industry
Industry/Entity Type
Real Estate
Contact Information for Business Card
name: Dale Harwick
position: Managing Member
address: 4821 Corliss Pkwy ste 207-300
N. Las Vegas, NV 89084
phone: (702) 555-0143
fax: (702) 555-0187
email: SummitRidgeEstate@hollowmail.test
web: SummitRidgeEstates.test
*At the bottom of the card I would like....
We buy houses for cash....no repairs, no commissions, no fees!
Logo Text
SUMMIT RIDGE ESTATES "Investing in Our Community"
Font styles to use
Other font styles liked:
- Lora
Requirements
Must have
- On the back of the card, i'd like to have my logo large and the following statements:
- Are you considering selling your home? Want a simple, hassle-free transaction? We can help! We buy houses for cash and can close quickly! No need to do any repairs, no realtor commissions, no closing costs.....and no headaches. Let us help you with your real estate needs...!
Nice to have
- multiple colors 2 two tone on front and back

```html
<!DOCTYPE html>
<html lang="en">
<head>
<meta charset="utf-8">
<title>Summit Ridge Estates – Business Card</title>
<link rel="stylesheet" href="https://fonts.googleapis.com/css2?family=Lora:wght@600&family=Montserrat:wght@400;500&family=Oswald:wght@600&display=swap">
<style>
  :root {
    --page: #2a2a2a;
    --card: #060606;
    --blue: #1f63c4;
    --grey: #a9a9a9;
    --white: #ffffff;
  }
  * { box-sizing: border-box; margin: 0; padding: 0; }
  html, body { width: 1200px; height: 900px; overflow: hidden; }
  body {
    background: var(--page);
    display: flex;
    flex-direction: column;
    align-items: center;
    justify-content: center;
    gap: 44px;
    font-family: "Montserrat", Arial, sans-serif;
    color: var(--white);
  }
  .card {
    width: 660px;
    height: 378px;
    background: var(--card);
    border-radius: 20px;
    position: relative;
    overflow: hidden;
  }

  /* Back side */
  .card-back {
    display: flex;
    flex-direction: column;
    align-items: center;
    padding-top: 92px;
  }
  .brand {
    display: flex;
    align-items: center;
    gap: 12px;
    font-family: "Lora", Georgia, serif;
    font-weight: 600;
    color: var(--blue);
    white-space: nowrap;
  }
  .brand-mark { background: var(--grey); display: block; }
  .card-back .brand { font-size: 40px; }
  .card-back .brand-mark { width: 30px; height: 30px; }
  .pitch {
    margin-top: 44px;
    text-align: center;
    font-size: 16px;
    line-height: 1.38;
    font-weight: 500;
  }

  /* Front side */
  .card-front .brand-block {
    position: absolute;
    top: 52px;
    left: 0;
    right: 0;
    display: flex;
    flex-direction: column;
    align-items: center;
    gap: 8px;
  }
  .card-front .brand { font-size: 30px; }
  .card-front .brand-mark { width: 22px; height: 22px; }
  .slogan {
    font-family: "Lora", Georgia, serif;
    font-size: 12px;
    letter-spacing: 3px;
    color: var(--white);
  }
  .divider {
    position: absolute;
    left: 318px;
    top: 150px;
    width: 1px;
    height: 128px;
    background: linear-gradient(to bottom, transparent, var(--white) 30%, var(--white) 70%, transparent);
  }
  .person {
    position: absolute;
    right: 360px;
    top: 228px;
    text-align: right;
  }
  .person-name {
    font-family: "Lora", Georgia, serif;
    font-weight: 600;
    font-size: 27px;
    color: var(--blue);
    white-space: nowrap;
  }
  .person-role { font-size: 16px; margin-top: 2px; }
  .contact {
    position: absolute;
    left: 340px;
    top: 152px;
    font-size: 14px;
    line-height: 1.35;
  }
  .address { margin-bottom: 12px; font-size: 15px; }
  .contact-list { list-style: none; }
  .contact-list li { display: flex; align-items: center; gap: 10px; white-space: nowrap; }
  .contact-list svg { width: 12px; height: 12px; fill: var(--blue); flex: none; }
  .accent { color: var(--blue); }
  .offer {
    position: absolute;
    left: 0;
    right: 0;
    bottom: 26px;
    display: flex;
    align-items: center;
    gap: 12px;
  }
  .offer-line { flex: 1; height: 3px; background: var(--blue); }
  .offer-text {
    font-family: "Oswald", Impact, sans-serif;
    font-weight: 600;
    font-size: 17px;
    letter-spacing: 0.3px;
    white-space: nowrap;
  }
</style>
</head>
<body>

<section class="card card-back">
  <div class="brand">
    <span class="brand-mark"></span>
    <span class="brand-name">SUMMIT RIDGE ESTATES</span>
  </div>
  <p class="pitch">
    Are you considering selling your home?<br>
    Want a simple, hassle-free transaction?<br>
    We can help! We buy houses for cash and can close quickly!<br>
    No need to do any repairs, no realtor commissions, no closing costs<br>
    and no headaches. Let us help you with your real estate needs...!
  </p>
</section>

<section class="card card-front">
  <div class="brand-block">
    <div class="brand">
      <span class="brand-mark"></span>
      <span class="brand-name">SUMMIT RIDGE ESTATES</span>
    </div>
    <p class="slogan">“Investing in Our Community”</p>
  </div>

  <div class="divider"></div>

  <div class="person">
    <p class="person-name">DALE HARWICK</p>
    <p class="person-role">Managing Member</p>
  </div>

  <div class="contact">
    <p class="address">4821 Corliss Pkwy ste 207-300<br>N. Las Vegas, NV 89084</p>
    <ul class="contact-list">
      <li>
        <svg viewBox="0 0 24 24" aria-hidden="true"><path d="M6.6 10.8a15.1 15.1 0 0 0 6.6 6.6l2.2-2.2c.3-.3.7-.4 1-.2 1.1.4 2.3.6 3.6.6.6 0 1 .4 1 1V20c0 .6-.4 1-1 1A17 17 0 0 1 3 4c0-.6.4-1 1-1h3.5c.6 0 1 .4 1 1 0 1.3.2 2.5.6 3.6.1.3 0 .7-.2 1z"/></svg>
        (702) 555-0143
      </li>
      <li>
        <svg viewBox="0 0 24 24" aria-hidden="true"><path d="M6 2h12v5H6zM4 8h16a2 2 0 0 1 2 2v7h-4v5H6v-5H2v-7a2 2 0 0 1 2-2zm4 8v4h8v-4z"/></svg>
        (702) 555-0187
      </li>
      <li>
        <svg viewBox="0 0 24 24" aria-hidden="true"><path d="M2 5h20v14H2zm2 2v.5l8 5 8-5V7zm0 2.8V17h16V9.8l-8 5z"/></svg>
        SummitRidgeEstate@hollowmail.test
      </li>
      <li>
        <svg viewBox="0 0 24 24" aria-hidden="true"><path d="M12 2a10 10 0 1 0 0 20 10 10 0 0 0 0-20zm6.9 9h-3a15 15 0 0 0-1.2-5.6A8 8 0 0 1 18.9 11zM12 4c.9 1.3 1.8 3.7 1.9 7h-3.8c.1-3.3 1-5.7 1.9-7zM9.3 5.4A15 15 0 0 0 8.1 11h-3a8 8 0 0 1 4.2-5.6zM5.1 13h3a15 15 0 0 0 1.2 5.6A8 8 0 0 1 5.1 13zM12 20c-.9-1.3-1.8-3.7-1.9-7h3.8c-.1 3.3-1 5.7-1.9 7zm2.7-1.4a15 15 0 0 0 1.2-5.6h3a8 8 0 0 1-4.2 5.6z"/></svg>
        <span>www.<span class="accent">SummitRidgeEstates</span>.test</span>
      </li>
    </ul>
  </div>

  <div class="offer">
    <span class="offer-line"></span>
    <span class="offer-text">WE BUY HOUSES FOR CASH....NO REPAIRS, NO COMMISSIONS, NO FEES!</span>
    <span class="offer-line"></span>
  </div>
</section>

</body>
</html>
```